"Harbor Builders" is a residential building company and needs a new business card design and may re

We would like a redesign based on the existing logo, and would like to see a new font as well. We are bespoke home builders who build sustainable energy efficient homes.

Industry/Entity Type

Construction

Contact Information for Business Card

Business card size 40mm x 90mm

Colors

Designer to choose colors to be used in the design.

```html
<!DOCTYPE html>
<html lang="en">
<head>
<meta charset="utf-8">
<title>Harbor Builders – Business Card</title>
<link rel="stylesheet" href="https://fonts.googleapis.com/css2?family=Open+Sans:wght@600&family=Roboto:wght@400;500&family=Roboto+Condensed:wght@700&display=swap">
<style>
  :root {
    --backdrop: #5b4a3b;
    --card: #f1f1f1;
    --ink: #0a0b0c;
    --lime: #b4cb2f;
    --white: #ffffff;
    --muted: #555555;
  }
  * { box-sizing: border-box; margin: 0; padding: 0; }
  html, body { width: 1200px; height: 960px; overflow: hidden; }
  body { background: var(--backdrop); position: relative; font-family: "Roboto", Arial, sans-serif; }

  .card { position: absolute; width: 600px; height: 343px; background: var(--card); overflow: hidden; }
  .card--front { left: 314px; top: 113px; }
  .card--back { left: 311px; top: 472px; }

  .card__bands { position: absolute; inset: 0; }

  .wordmark { position: absolute; display: flex; align-items: center; gap: 12px;
    font-family: "Open Sans", Arial, sans-serif; font-weight: 600; color: var(--ink); white-space: nowrap; }
  .wordmark__square { background: var(--lime); flex: none; }
  .card--front .wordmark { left: 0; right: 0; top: 58px; justify-content: center; font-size: 36px; }
  .card--front .wordmark__square { width: 28px; height: 28px; }
  .card--back .wordmark { left: 0; right: 0; top: 120px; justify-content: center; font-size: 50px; gap: 18px; }
  .card--back .wordmark__square { width: 42px; height: 42px; }

  .holder { position: absolute; left: 28px; top: 232px; color: var(--white); }
  .holder__name { font-family: "Roboto Condensed", Arial, sans-serif; font-weight: 700; font-size: 21px;
    color: var(--lime); letter-spacing: 0.2px; margin-bottom: 14px; }
  .holder__company { font-weight: 500; font-size: 14.5px; line-height: 19px; }
  .holder__address { font-size: 14.5px; line-height: 19px; }

  .contact { position: absolute; right: 24px; top: 229px; text-align: right; color: var(--ink); font-size: 14.5px; }
  .contact__reg { line-height: 18px; }
  .contact__list { list-style: none; margin-top: 6px; }
  .contact__item { display: flex; justify-content: flex-end; align-items: center; gap: 6px; line-height: 19px; }
  .contact__icon { width: 13px; height: 13px; flex: none; }

  .site { position: absolute; left: 0; right: 0; top: 298px; text-align: center;
    font-size: 14px; letter-spacing: 3px; color: var(--muted); }
</style>
</head>
<body>

<section class="card card--front">
  <svg class="card__bands" width="600" height="343" viewBox="0 0 600 343" aria-hidden="true">
    <polygon points="0,142 298,243 298,343 0,343" fill="var(--ink)"/>
    <polygon points="302,243 600,142 600,343 302,343" fill="var(--lime)"/>
  </svg>

  <div class="wordmark"><span class="wordmark__square"></span>Harbor Builders</div>

  <div class="holder">
    <p class="holder__name">DANIEL MARSH</p>
    <p class="holder__company">Harbor Builders Pty Ltd</p>
    <p class="holder__address">PO Box 4120 Eastgate</p>
    <p class="holder__address">LPO Hillside WA 6090</p>
  </div>

  <div class="contact">
    <p class="contact__reg">Registration 30418</p>
    <p class="contact__reg">ABN: 42 305 118 764</p>
    <ul class="contact__list">
      <li class="contact__item">0412 555 308
        <svg class="contact__icon" viewBox="0 0 13 13" aria-hidden="true"><rect x="3" y="0.5" width="7" height="12" rx="1.2" fill="none" stroke="var(--ink)" stroke-width="1.4"/><rect x="5.5" y="10" width="2" height="1" fill="var(--ink)"/></svg>
      </li>
      <li class="contact__item">daniel@harborbuilders.com.au
        <svg class="contact__icon" viewBox="0 0 13 13" aria-hidden="true"><rect x="0.5" y="3" width="12" height="8" fill="var(--ink)"/><polyline points="0.5,3 6.5,7.5 12.5,3" fill="none" stroke="var(--lime)" stroke-width="1"/></svg>
      </li>
      <li class="contact__item">www.harborbuilders.com.au
        <svg class="contact__icon" viewBox="0 0 13 13" aria-hidden="true"><circle cx="6.5" cy="6.5" r="6" fill="var(--ink)"/><path d="M3 4 Q6 5 5 8 Q8 9 9 11 M8 2 Q10 4 11 5" fill="none" stroke="var(--lime)" stroke-width="1"/></svg>
      </li>
    </ul>
  </div>
</section>

<section class="card card--back">
  <div class="wordmark"><span class="wordmark__square"></span>Harbor Builders</div>
  <p class="site">www.harborbuilders.com.au</p>
</section>

</body>
</html>
```